sydney wedding photography business needs a business card design

we need a business card design for a sydney based wedding photography and videography business. our business name is :golden hour studio and film. our target clients are 24-35 yrs female. our style is candid, organic, natural, dynamic. we are a team of young photographers and videographers, and help brides to create memories that they will cherish for the rest of their lives. the logo will be provided. we want an elegant design that reflects our style, and also want to give a great impression to our clients that we are one of the best studios in sydney and our brand means quality and premium service.

Target Market(s)

bride to be, 24-35 years old, living in sydney and surrunding areas

Industry/Entity Type

Wedding Photography

Contact Information for Business Card

address: 57 tarrant street, glenmore nsw 2047
mobile: 0431872259
phone: (02) 9163 2408
info@tidewillowstudio.net.au
www.tidewillowstudio.net.au
facebook:tidewillowweddings
instagram:tidewillowweddings

Font styles to use
Serif
Sans Serif

Requirements
Nice to have
• maybe add my slogan"memories beyond eternity" if the layout looks good
Should not have
• no black color, not good idea for wedding biz card

```html
<!DOCTYPE html>
<html lang="en">
<head>
<meta charset="utf-8">
<title>Golden Hour Studio and Film – Business Card</title>
<link href="https://fonts.googleapis.com/css2?family=Source+Sans+3:wght@400;600&display=swap" rel="stylesheet">
<style>
  :root {
    --backdrop: #000000;
    --card: #4d4c52;
    --card-edge: #5a5960;
    --gold: #e8b01c;
    --ink-light: #f4f2ee;
    --divider: #3c3b40;
  }
  * { box-sizing: border-box; margin: 0; padding: 0; }
  html, body {
    width: 1200px; height: 900px; overflow: hidden;
    background: var(--backdrop);
    font-family: "Source Sans 3", "Myriad Pro", sans-serif;
  }
  .stage { position: relative; width: 1200px; height: 900px; }
  .card {
    position: absolute; top: 271px;
    width: 457px; height: 282px;
    border-radius: 14px;
    background: radial-gradient(ellipse at 50% 40%, var(--card-edge), var(--card) 70%);
  }
  .card--front { left: 137px; }
  .card--back { left: 627px; }

  .front-mark {
    position: absolute; left: 40px; top: 125px; width: 170px;
    text-align: center; color: var(--gold);
    font-weight: 600; font-size: 26px; line-height: 1.1;
  }
  .front-divider {
    position: absolute; left: 229px; top: 60px;
    width: 1px; height: 168px; background: var(--divider);
  }
  .details { position: absolute; left: 243px; top: 48px; color: var(--ink-light); font-size: 13px; line-height: 16.5px; }
  .details__name { color: var(--gold); font-weight: 600; font-size: 15px; line-height: 18px; }
  .details__title { margin-bottom: 9px; }
  .details__address { margin-bottom: 10px; }
  .contact { display: flex; align-items: center; gap: 7px; white-space: nowrap; }
  .contact svg { width: 10px; height: 10px; fill: var(--gold); flex: none; }

  .back-mark {
    position: absolute; left: 0; right: 0; top: 108px;
    text-align: center; color: var(--gold); font-weight: 600;
  }
  .back-mark__name { font-size: 38px; line-height: 40px; }
  .back-mark__line { font-size: 14px; letter-spacing: 6px; margin-top: 6px; }
</style>
</head>
<body>
<main class="stage">
  <section class="card card--front">
    <div class="front-mark">Golden Hour</div>
    <div class="front-divider"></div>
    <div class="details">
      <p class="details__name">Daniel Hartley</p>
      <p class="details__title">Managing Director</p>
      <p class="details__address">57 tarrant street,<br>glenmore nsw 2047</p>
      <p class="contact">
        <svg viewBox="0 0 10 10" aria-hidden="true"><rect x="2.5" y="0.5" width="5" height="9" rx="1"/></svg>
        0431872259
      </p>
      <p class="contact">
        <svg viewBox="0 0 10 10" aria-hidden="true"><path d="M2 0.5 L3.6 2.6 L2.8 3.6 Q4 6 6.4 7.2 L7.4 6.4 L9.5 8 L8.2 9.5 Q2 8.6 0.5 1.8 Z"/></svg>
        (02) 9163 2408
      </p>
      <p class="contact">
        <svg viewBox="0 0 10 10" aria-hidden="true"><path d="M0.5 2 H9.5 V8 H0.5 Z M0.8 2.3 L5 5.5 L9.2 2.3" stroke="#4d4c52" stroke-width="0.8"/></svg>
        info@tidewillowstudio.net.au
      </p>
      <p class="contact">
        <svg viewBox="0 0 10 10" aria-hidden="true"><circle cx="5" cy="5" r="4.5"/></svg>
        www.tidewillowstudio.net.au
      </p>
      <p class="contact">
        <svg viewBox="0 0 10 10" aria-hidden="true"><rect x="1" y="1" width="8" height="8" rx="1.5"/></svg>
        facebook: tidewillowweddings
      </p>
      <p class="contact">
        <svg viewBox="0 0 10 10" aria-hidden="true"><rect x="1" y="1" width="8" height="8" rx="1.5"/></svg>
        instagram: tidewillowweddings
      </p>
    </div>
  </section>

  <section class="card card--back">
    <div class="back-mark">
      <p class="back-mark__name">Golden Hour</p>
      <p class="back-mark__line">STUDIO AND FILM</p>
    </div>
  </section>
</main>
</body>
</html>
```